RW Framewell Inc Business cards

We need business cards using our existing logo but slightly modified. Right now the logo says RW Loadbearing Masonry. We want to keep the RW part of the design, but replace the Structural Concrete portion with "FRAMEWELL". Please see the attached file.
Ideally this would be a blank template so we can add Different Names, titles, and phone numbers later.
On the one side we want only the logo and on the other side the detail. I'm attaching an example for you to see.
Please reach out with any other questions. Our address and other details will be given out once we find a design we like.

Target Market(s)

Construction Industry

```html
<!DOCTYPE html>
<html lang="en">
<head>
<meta charset="utf-8">
<title>RW Framewell Inc Business Cards</title>
<link rel="stylesheet" href="https://fonts.googleapis.com/css2?family=Montserrat:wght@600&family=Roboto:wght@400;500&display=swap">
<style>
  :root {
    --backdrop: #4a4a4c;
    --card: #1e1f22;
    --brand-blue: #2f65b0;
    --ink-light: #f2f2f2;
    --ink-muted: #d6d6d6;
  }
  html, body {
    margin: 0;
    padding: 0;
    width: 799px;
    height: 1200px;
    overflow: hidden;
    background: var(--backdrop);
  }
  .canvas {
    position: relative;
    width: 799px;
    height: 1200px;
  }
  .card {
    position: absolute;
    left: 60px;
    width: 680px;
    height: 390px;
    background: var(--card);
    border-radius: 6px;
    box-shadow: 0 12px 30px rgba(0,0,0,0.45);
    overflow: hidden;
  }
  .card--front { top: 150px; }
  .card--back { top: 660px; }

  .wordmark {
    display: flex;
    align-items: center;
    gap: 14px;
    font-family: "Montserrat", sans-serif;
    font-weight: 600;
    color: var(--ink-light);
    letter-spacing: 0.12em;
    white-space: nowrap;
  }
  .wordmark__square {
    background: var(--brand-blue);
    flex: none;
  }
  .card--front .wordmark {
    position: absolute;
    left: 50%;
    top: 50%;
    transform: translate(-50%, -50%);
    font-size: 40px;
  }
  .card--front .wordmark__square { width: 26px; height: 26px; }

  .card--back .wordmark {
    position: absolute;
    right: 48px;
    top: 70px;
    font-size: 28px;
  }
  .card--back .wordmark__square { width: 18px; height: 18px; }

  .accent-arc {
    position: absolute;
    left: -22px;
    top: 38px;
    width: 44px;
    height: 44px;
    border-radius: 50%;
    background: var(--brand-blue);
  }
  .person {
    position: absolute;
    left: 44px;
    top: 40px;
    font-family: "Roboto", sans-serif;
  }
  .person__name {
    margin: 0;
    font-size: 22px;
    font-weight: 500;
    color: var(--brand-blue);
  }
  .person__title {
    margin: 4px 0 0;
    font-size: 15px;
    color: var(--ink-light);
  }
  .contact {
    position: absolute;
    left: 44px;
    top: 132px;
    margin: 0;
    padding: 0;
    list-style: none;
    font-family: "Roboto", sans-serif;
    font-size: 16px;
    color: var(--ink-light);
  }
  .contact__item {
    display: flex;
    align-items: center;
    gap: 12px;
    height: 26px;
  }
  .contact__icon { width: 14px; height: 14px; fill: var(--brand-blue); flex: none; }
  .divider {
    position: absolute;
    left: 44px;
    right: 48px;
    top: 242px;
    height: 1px;
    background: var(--brand-blue);
  }
  .address {
    position: absolute;
    right: 48px;
    top: 270px;
    margin: 0;
    text-align: right;
    font-family: "Roboto", sans-serif;
    font-style: normal;
    font-size: 17px;
    line-height: 1.45;
    color: var(--ink-light);
  }
</style>
</head>
<body>
<main class="canvas">
  <section class="card card--front" aria-label="Card front">
    <div class="wordmark"><span class="wordmark__square"></span>RW FRAMEWELL</div>
  </section>

  <section class="card card--back" aria-label="Card back">
    <span class="accent-arc"></span>
    <div class="person">
      <h1 class="person__name">Daniel RW Hart</h1>
      <p class="person__title">Managing Director</p>
    </div>
    <ul class="contact">
      <li class="contact__item">
        <svg class="contact__icon" viewBox="0 0 16 16" aria-hidden="true"><path d="M3.6 1.2l2.3 2.9-1.4 1.8c.9 2 2.6 3.7 4.6 4.6l1.8-1.4 2.9 2.3-1.3 2.4C7 13.6 2.4 9 1.2 3.6z"/></svg>
        555-014-2270
      </li>
      <li class="contact__item">
        <svg class="contact__icon" viewBox="0 0 16 16" aria-hidden="true"><path d="M1 3h14v10H1z M2.5 4.5v.3L8 9l5.5-4.2v-.3z" fill-rule="evenodd"/></svg>
        daniel@framewellco.com
      </li>
      <li class="contact__item">
        <svg class="contact__icon" viewBox="0 0 16 16" aria-hidden="true"><circle cx="8" cy="8" r="7"/><path d="M1 8h14M8 1c-3 3.5-3 10.5 0 14M8 1c3 3.5 3 10.5 0 14" stroke="#1e1f22" stroke-width="1.1" fill="none"/></svg>
        www.framewellco.com
      </li>
    </ul>
    <div class="divider"></div>
    <div class="wordmark"><span class="wordmark__square"></span>RW FRAMEWELL</div>
    <address class="address">118 Timber Row, Cedar Falls,<br>California, US 95012</address>
  </section>
</main>
</body>
</html>
```